Thoroughbred Racing Partnership needs web design

Glimmer of Laurel Partners is a management group who buys horses and races them on both the West and East coasts. The premise of the business is for an investment as little as $500, anyone can be a partner and own a percentage of a horse(s). This is a low cost way of getting involved in the exciting sport of Thoroughbred Racing, without shouldering the heavy financial responsibility. Our target market is mostly males 40+ but we want to include all target markets. We are looking for something very clean and professional, we want to give an image of success. Nothing overly "artsy." I have included the logo in which you can incorporate in the site. Also, the logo colors will be the colors of our "silks." The silks are what the jockey wears and will be an important marketing tool for GOL. We would like a very prominent picture of a racehorse somewhere on the homepage, we want to make it clear that is a website for Horseracing partnerships.

On the top of the site, it should say "Glimmer of Laurel" (on the top)
and below that "Thoroughbred Racing Partnerships." (below that)

The main sections, which should be across the top are:

Home
About Us
Ownership
Stable Roster
News
Contact us

Some of these will have drop down menus.

An example of a competitor website that we like is: www.harrowgatefarm.example
An example of a competitor website that we don't like is: www.paddockvue.example
Updates

Project Deadline Extended
Reason: We have a Board of Directors meeting on the 22nd and we will be making a decision on that day. I'm giving an extension so that all designers are able to submit their designs by the 22nd. Thank you!

Target Market(s)

40+ males

Industry/Entity Type

Business

Requirements
Must have
• our logo must be on the site. We would like at least one bold image of a thoroughbred horse in action. The picture is going to tell the story so it needs to be very eye-catching.

Our slogan should also be included on the website, "Experience the thrill of owning a Racehorse."
Should not have
• cartoons, artsy pictures, pictures of Steeplechase horses or "jumpers." This partnership is for racehorses only, there is not jumping involved with the horses.

```html
<!DOCTYPE html>
<html lang="en">
<head>
<meta charset="utf-8">
<title>Glimmer of Laurel Partners</title>
<link href="https://fonts.googleapis.com/css2?family=Montserrat:wght@500;600;700&family=Arimo:wght@400&display=swap" rel="stylesheet">
<style>
  :root{
    --navy:#0f2f66;
    --navy-deep:#0a2452;
    --band:#25669a;
    --band-dark:#1d5789;
    --sky-top:#6fb4e6;
    --sky-mid:#a9d6f4;
    --sky-low:#d6ecfa;
    --phone:#a9c9e4;
    --white:#ffffff;
    --text:#222222;
    --footer:#dcdcdc;
    --footer-muted:#a6a6a6;
    --footer-logo:#9a9a9a;
  }
  *{margin:0;padding:0;box-sizing:border-box}
  html,body{width:1200px;height:879px;overflow:hidden;background:var(--white)}
  body{position:relative;font-family:"Arimo",Arial,sans-serif;color:var(--text)}

  .hero{position:absolute;left:0;top:0;width:1200px;height:477px;
    background:radial-gradient(ellipse at 30% 55%,var(--sky-low) 0%,var(--sky-mid) 40%,var(--sky-top) 100%)}
  .top-band{position:absolute;left:0;top:8px;width:1200px;height:62px;background:linear-gradient(var(--band),var(--band-dark))}
  .logo-tab{position:absolute;left:0;top:0}
  .brand{position:absolute;left:150px;top:46px;width:264px;text-align:center;white-space:nowrap;
    font-family:"Montserrat",Arial,sans-serif;font-weight:700;font-size:28px;color:var(--navy)}

  .social{position:absolute;top:23px;left:653px;display:flex;gap:4px}
  .social span{width:29px;height:29px;border-radius:50%;background:#a7c5e0;display:flex;align-items:center;justify-content:center}
  .divider{position:absolute;left:811px;top:8px;width:1px;height:62px;background:#3f7aab}
  .phone{position:absolute;left:836px;top:22px;display:flex;align-items:center;gap:12px;
    font-family:"Montserrat",Arial,sans-serif;font-weight:600;font-size:21px;color:var(--phone)}

  .nav{position:absolute;top:88px;left:0;font-family:"Montserrat",Arial,sans-serif;font-weight:600;font-size:12px;color:var(--white)}
  .nav a{position:absolute;white-space:nowrap;text-decoration:none;color:inherit}
  .nav .caret::after{content:"";display:inline-block;margin-left:9px;border-left:4px solid transparent;border-right:4px solid transparent;border-top:6px solid var(--white);vertical-align:1px}

  .hero-photo{position:absolute;left:21px;top:200px;width:673px;height:277px;
    border-radius:45% 55% 0 0 / 60% 60% 0 0;
    background:radial-gradient(ellipse at 50% 55%,#7a3d1f 0%,#5a2c17 45%,rgba(90,44,23,.2) 80%,rgba(90,44,23,0) 100%)}

  .hero-copy{position:absolute;left:668px;top:205px;width:400px;text-align:center;font-family:"Montserrat",Arial,sans-serif;white-space:nowrap}
  .hero-title{font-weight:700;font-size:35px;color:var(--navy);letter-spacing:-.5px;line-height:44px}
  .hero-sub{font-weight:500;font-size:17px;color:var(--white);line-height:22px;margin-top:2px}
  .cta{position:absolute;left:720px;top:294px;width:300px;height:64px;border-radius:6px;
    background:linear-gradient(#1d5592,var(--navy-deep));box-shadow:0 4px 8px rgba(0,0,0,.3);
    display:flex;align-items:center;justify-content:center;gap:16px;
    font-family:"Montserrat",Arial,sans-serif;font-weight:700;font-size:16px;color:var(--white)}

  .photo-card{position:absolute;left:732px;top:437px;width:338px;height:227px;background:var(--white);
    border-radius:6px;box-shadow:0 6px 14px rgba(0,0,0,.2)}
  .photo-card .photo{position:absolute;left:9px;top:8px;width:321px;height:213px;
    background:linear-gradient(#6b6a5a 0%,#6e3d22 40%,#4f7a34 80%,#5d8a3c 100%)}

  .intro{position:absolute;left:160px;top:515px;width:530px}
  .intro h1{font-family:"Montserrat",Arial,sans-serif;font-weight:700;font-size:21.5px;line-height:28px;color:var(--navy);letter-spacing:-.4px;white-space:nowrap}
  .intro p{margin-top:16px;margin-left:2px;width:528px;font-size:11px;line-height:19px;color:var(--text)}
  .read-more{position:absolute;left:589px;top:625px;font-family:"Montserrat",Arial,sans-serif;font-weight:600;font-size:14px;color:var(--navy);text-decoration:underline}

  .footer{position:absolute;left:0;top:714px;width:1200px;height:165px;background:var(--footer);box-shadow:inset 0 6px 8px -6px rgba(0,0,0,.2)}
  .sitemap-title{position:absolute;left:164px;top:58px;font-family:"Montserrat",Arial,sans-serif;font-weight:600;font-size:18px;color:var(--footer-muted)}
  .sitemap a{position:absolute;font-size:11px;color:#222;text-decoration:none}
  .company{position:absolute;right:381px;top:60px;text-align:right;white-space:nowrap}
  .company h2{font-family:"Montserrat",Arial,sans-serif;font-weight:600;font-size:18px;color:var(--footer-muted)}
  .company p{font-size:11px;line-height:18px;color:#111;margin-top:4px}
  .footer-brand{position:absolute;left:852px;top:68px;width:190px;text-align:center;white-space:nowrap;
    font-family:"Montserrat",Arial,sans-serif;font-weight:700;font-size:24px;color:var(--footer-logo)}
</style>
</head>
<body>

<section class="hero">
  <div class="hero-photo" role="img" aria-label="Two thoroughbred racehorses with jockeys in red silks galloping at full stride"></div>

  <div class="hero-copy">
    <div class="hero-title">Glimmer of Laurel</div>
    <div class="hero-sub">Thoroughbred Racing Partnerships.</div>
  </div>
  <a class="cta">Learn About Partnerships
    <svg width="14" height="22" viewBox="0 0 14 22"><path d="M2 2 L11 11 L2 20" fill="none" stroke="#fff" stroke-width="4"/></svg>
  </a>
</section>

<div class="top-band"></div>
<svg class="logo-tab" width="480" height="130" viewBox="0 0 480 130">
  <path d="M50 0 H480 C445 0 432 18 420 38 L405 70 C390 100 365 127 320 127 H200 C160 127 140 110 125 90 L100 55 C85 30 72 8 50 0 Z" fill="#ffffff"/>
  <path d="M470 70 L480 70 L472 78 Z" fill="#1d5789"/>
</svg>
<div class="brand">GOL Partners</div>

<div class="social">
  <span></span>
  <span></span>
  <span><svg width="14" height="11" viewBox="0 0 14 11"><rect x="1" y="1" width="12" height="9" fill="none" stroke="#fff" stroke-width="1.5"/><path d="M1 1 L7 6 L13 1" fill="none" stroke="#fff" stroke-width="1.5"/></svg></span>
  <span></span>
</div>
<div class="divider"></div>
<div class="phone">
  <svg width="24" height="24" viewBox="0 0 24 24"><path d="M6 2 C3 3 2 6 4 10 C7 16 11 20 16 22 C19 23 21 21 22 18 L18 14 L15 16 C12 14 10 12 8 9 L10 6 Z" fill="none" stroke="#a9c9e4" stroke-width="2"/></svg>
  <span>1800-5550 1234</span>
</div>

<nav class="nav">
  <a style="left:452px">HOME</a>
  <a class="caret" style="left:536px">ABOUT US</a>
  <a style="left:635px">OWNERSHIP</a>
  <a class="caret" style="left:738px">STABLE ROSTER</a>
  <a style="left:885px">NEWS</a>
  <a style="left:966px">CONTACT US</a>
</nav>

<div class="photo-card">
  <div class="photo" role="img" aria-label="Field of racehorses and jockeys charging across a turf track"></div>
</div>

<section class="intro">
  <h1>Experience the thrill of owning a Racehorse.</h1>
  <p>Lorem ipsum dolor sit amet, consectetur adipiscing elit. Donec eleifend diam id vulputate dictum. Morbi sagittis dui sit amet ultricies pharetra. Vestibulum sagittis turpis a fermentum interdum. Mauris sapien arcu, sollicitudin at diam eget, posuere lobortis turpis. Morbi nisi odio, congue eu leo a, sollicitudin congue leo.</p>
</section>
<a class="read-more">READ MORE</a>

<footer class="footer">
  <div class="sitemap-title">Sitemap</div>
  <div class="sitemap">
    <a style="left:164px;top:90px">Home</a>
    <a style="left:164px;top:109px">About Us</a>
    <a style="left:260px;top:90px">Stable Roster</a>
    <a style="left:260px;top:109px">News</a>
    <a style="left:356px;top:90px">Ownership</a>
    <a style="left:356px;top:109px">Contact us</a>
  </div>
  <div class="company">
    <h2>GOL Partners</h2>
    <p>Lorem ipsum Street it amet, consectetur adipiscing elit. Donec<br>P: 1800 - 5550 1234, E: hello@golpartners.example</p>
  </div>
  <div class="footer-brand">GOL Partners</div>
</footer>

</body>
</html>
```